BRIVAN 2026 Flyer for Conference

BRIVAN needs a design for a 1-page flyer that we will hand out at an upcoming event & then later post online as a pdf. There are 3 elements which need to be on the flyer:

1) A logo. This should be prominent on the design (e.g., in the middle). The flyer should use the colors that are in that logo (e.g., for accents, design elements, and/or text; not all of these have to be used):
Dark blue: #185577
Med blue: #327C9A
Teal: #4EB1C2
Light Teal: #9EDBE6

2) The conference theme -- Oceans of Knowledge: Diving into Information Literacy -- should be at the flyer's top.

3) Finally, these six tracks should be listed below the theme and the logo (it's font size should be at least a couple sizes smaller than the size used for the theme):
- Pearls of Pedagogy: Teaching Techniques that Work
- The Depth Gauge: Measuring Instructional Impact
- Techtonic Shifts: Innovation and Educational Technology
- Captain's Log: Navigating Leadership in Library Instruction
- Swimming Together: Collaborating with Others
- The Bermuda Triangle: Exploring (Seemingly) Eternal Challenges

Font styles to use
Sans Serif

Colors
0094D4
00A9DD
6FCCEA
C7EBF8
E9F6FB

Requirements
Must have
• The 3 elements listed in the description: 1) the logo, 2) the text of the theme and 3) the text for the tracks.

```html
<!DOCTYPE html>
<html lang="en">
<head>
<meta charset="utf-8">
<title>BRIVAN 2026 – Oceans of Knowledge</title>
<link href="https://fonts.googleapis.com/css2?family=Poppins:wght@400;600;700;800&display=swap" rel="stylesheet">
<style>
  :root {
    --page: #ffffff;
    --deep: #0b2f8c;
    --ocean: #1747b8;
    --reef: #2f8a96;
    --abyss: #0c2a36;
    --dark-blue: #185577;
    --med-blue: #327C9A;
    --teal: #4EB1C2;
    --light-teal: #9EDBE6;
    --headline: #45d7ea;
    --headline-light: #8fe3f2;
    --white: #ffffff;
  }
  * { box-sizing: border-box; margin: 0; padding: 0; }
  html, body { width: 1021px; height: 1200px; overflow: hidden; background: var(--page); }
  body { position: relative; font-family: "Poppins", sans-serif; }

  .flyer {
    position: absolute; left: 120px; top: 95px; width: 781px; height: 1009px;
    overflow: hidden;
  }
  .underwater-scene {
    position: absolute; inset: 0;
    background:
      radial-gradient(ellipse 45% 30% at 50% 78%, rgba(60,140,120,0.85), rgba(60,140,120,0) 70%),
      radial-gradient(ellipse 60% 25% at 50% 62%, rgba(40,150,170,0.7), rgba(40,150,170,0) 75%),
      linear-gradient(180deg, var(--ocean) 0%, var(--deep) 18%, #1a46a8 40%, #2a6aa0 55%, var(--reef) 70%, #15414c 85%, var(--abyss) 100%);
  }
  .bookshelves { position: absolute; left: 0; top: 0; width: 781px; height: 1009px; }

  .event-mark {
    position: absolute; left: 0; right: 0; top: 62px; text-align: center;
  }
  .event-mark .badge {
    display: inline-block; background: var(--light-teal); border-radius: 50%;
    width: 22px; height: 22px; vertical-align: middle; margin-right: 10px;
  }
  .event-mark .name { font-weight: 800; font-size: 50px; line-height: 1; vertical-align: middle; color: var(--light-teal); }
  .event-details {
    position: absolute; left: 0; right: 0; top: 148px; text-align: center;
    font-size: 11px; font-weight: 600; letter-spacing: 2px; color: var(--teal);
  }
  .presents {
    position: absolute; left: 0; right: 0; top: 188px; text-align: center;
    font-size: 20px; font-weight: 600; letter-spacing: 5px; color: var(--white);
  }
  .theme-title { position: absolute; left: 0; right: 0; top: 232px; text-align: center; font-weight: 800; line-height: 1; }
  .theme-title .big { display: block; font-size: 114px; color: var(--headline-light); letter-spacing: 1px; }
  .theme-title .sub { display: block; font-size: 72px; color: var(--headline); margin-top: 2px; letter-spacing: -0.5px; }
  .theme-tagline {
    position: absolute; left: 0; right: 0; top: 420px; text-align: center;
    font-size: 26px; font-weight: 700; line-height: 1.1; color: var(--white);
  }

  .tracks { position: absolute; top: 784px; left: 0; width: 781px; }
  .track { position: absolute; width: 265px; list-style: none; }
  .track h3 { font-size: 13.5px; font-weight: 800; color: var(--headline); line-height: 1.2; text-transform: uppercase; position: relative; }
  .track h3::before {
    content: ""; position: absolute; left: -12px; top: 4px; width: 7px; height: 7px;
    border-radius: 50%; background: var(--headline);
  }
  .track p { font-size: 14.5px; color: var(--white); line-height: 1.25; }
  .col-a { left: 132px; }
  .col-b { left: 401px; }

  .site-url {
    position: absolute; left: 0; right: 0; top: 960px; text-align: center;
    font-size: 13px; letter-spacing: 3.5px; color: var(--white);
  }
  .site-url span { color: var(--headline); }
</style>
</head>
<body>
  <main class="flyer">
    <div class="underwater-scene" role="img" aria-label="Underwater photograph with sunlight on the surface and a coral reef on the sea floor"></div>

    <svg class="bookshelves" viewBox="0 0 781 1009" role="img" aria-label="Curved library bookshelves full of books lining both sides of the reef">
      <defs>
        <linearGradient id="shelfShade" x1="0" y1="0" x2="1" y2="0">
          <stop offset="0" stop-color="#5f7891"/>
          <stop offset="1" stop-color="#a9bccd"/>
        </linearGradient>
        <linearGradient id="shelfShadeR" x1="1" y1="0" x2="0" y2="0">
          <stop offset="0" stop-color="#5f7891"/>
          <stop offset="1" stop-color="#a9bccd"/>
        </linearGradient>
      </defs>
      <path d="M0 344 Q170 410 247 517 Q150 700 75 880 L0 925 Z" fill="url(#shelfShade)" opacity="0.9"/>
      <path d="M781 344 Q611 410 534 517 Q631 700 706 880 L781 925 Z" fill="url(#shelfShadeR)" opacity="0.9"/>
    </svg>

    <header class="event-mark">
      <span class="badge"></span><span class="name">BRIVAN 2026</span>
    </header>
    <p class="event-details">NORFOLK, VA · MAY 7-9</p>

    <p class="presents">presents</p>

    <h1 class="theme-title">
      <span class="big">OCEANS</span>
      <span class="sub">OF KNOWLEDGE</span>
    </h1>
    <p class="theme-tagline">Diving into Information Literacy</p>

    <ul class="tracks">
      <li class="track col-a" style="top:0"><h3>Pearls of Pedagogy:</h3><p>Teaching Techniques that Work</p></li>
      <li class="track col-a" style="top:44px"><h3>Techtonic Shifts:</h3><p>Innovation and<br>Educational Technology</p></li>
      <li class="track col-a" style="top:105px"><h3>The Bermuda Triangle:</h3><p>Exploring (Seemingly)<br>Eternal Challenges</p></li>
      <li class="track col-b" style="top:0"><h3>Captain's Log:</h3><p>Navigating Leadership in<br>Library Instruction</p></li>
      <li class="track col-b" style="top:63px"><h3>Swimming Together:</h3><p>Collaborating with Others</p></li>
      <li class="track col-b" style="top:105px"><h3>The Depth Gauge:</h3><p>Measuring Instructional Impact</p></li>
    </ul>

    <p class="site-url">www.<span>brivanconference</span>.org</p>
  </main>
</body>
</html>
```